Create a web design for a vehicle codes lookup website

Create a bright and fun web design to replace our current boring one!

-Make a new design for this page that shows vehicle codes information: http://plexora.site/vin/dara-pellow.4182.html
-Click "Random VIN" to see more examples.
-The page shows the vehicle information (see above example) is the most important one to add a redesign to. Bonus points if you create a redesign for the main page as well: plexora.site.

Number of Pages Required

2 page

Requirements
Must have
• Be fun and have bright colors!
Should not have
• Do not add pictures of specific people or vehicles unless they can be used on every page. The example page has a Morvane Tessly, but do not add a picture of the Morvane Tessly because other pages have different vehicles.

```html
<!DOCTYPE html>
<html lang="en">
<head>
<meta charset="utf-8">
<title>Vehicle Purchase Records Database</title>
<link href="https://fonts.googleapis.com/css2?family=Raleway:wght@300;400;600;700&family=Open+Sans:wght@400;600;700&display=swap" rel="stylesheet">
<style>
:root{
  --navy:#1e2f8c;
  --navy-deep:#162370;
  --tile-red:#c8332e;
  --tile-dark:#2a2f45;
  --tile-grey:#8a8f9c;
  --tile-tan:#b08d52;
  --green:#3f9a52;
  --green-light:#5bb46c;
  --amber:#e8a21a;
  --amber-deep:#d98a10;
  --sky:#9fbde3;
  --sky-light:#c7d9ef;
  --crimson:#d0504c;
  --crimson-deep:#b73a37;
  --footer:#2b1212;
  --ink:#2a2a2a;
  --white:#ffffff;
}
*{margin:0;padding:0;box-sizing:border-box}
html,body{width:1200px;height:2868px;overflow:hidden}
body{font-family:"Open Sans",Arial,sans-serif;color:var(--white);background:var(--navy-deep);position:relative}
section,header,footer{position:absolute;left:0;width:1200px}

/* header + nav */
.masthead{top:0;height:432px;background:linear-gradient(180deg,var(--navy-deep) 0,var(--navy) 60%,#2a43b0 100%)}
.masthead__bar{height:88px;display:flex;align-items:center;justify-content:space-between;padding:0 225px;background:rgba(0,0,0,.18)}
.brand{font-family:"Raleway",sans-serif;font-size:22px;letter-spacing:2px;font-weight:400}
.brand strong{font-weight:700}
.utility-nav{font-size:12px;letter-spacing:1.5px;opacity:.8;text-transform:uppercase}
.tiles{position:absolute;top:310px;left:220px;width:780px;height:92px;display:flex;gap:4px}
.tile{flex:1;display:flex;flex-direction:column;justify-content:center;align-items:center;font-family:"Raleway",sans-serif;text-transform:uppercase;font-size:15px;font-weight:700;letter-spacing:1px;line-height:1.3}
.tile span{font-weight:400;font-size:12px;opacity:.85}
.tile--red{background:var(--tile-red)}
.tile--dark{background:var(--tile-dark)}
.tile--grey{background:var(--tile-grey)}
.tile--tan{background:var(--tile-tan)}

/* search */
.search{top:432px;height:240px;background:var(--green);text-align:center}
.search h1{font-family:"Raleway",sans-serif;font-weight:400;font-size:30px;margin-top:50px}
.search__form{width:720px;margin:34px auto 0;display:grid;grid-template-columns:repeat(4,auto);gap:14px 12px;align-items:center;justify-content:center}
.search__form label{font-size:12px;text-transform:uppercase;letter-spacing:1px;text-align:right}
.search__field{width:220px;height:26px;background:var(--white);border:1px solid var(--green-light)}

/* about */
.about{top:672px;height:680px;background:linear-gradient(160deg,var(--amber) 0,var(--amber-deep) 100%);overflow:hidden}
.about__photo{position:absolute;right:0;top:40px;width:900px;height:620px;background:radial-gradient(ellipse at 60% 45%,rgba(255,220,140,.55) 0,rgba(230,140,20,.25) 55%,rgba(0,0,0,0) 75%)}
.badge{position:absolute;width:128px;height:128px;border-radius:50%;border:6px solid rgba(255,255,255,.75);display:flex;align-items:center;justify-content:center;font-family:"Raleway",sans-serif;font-size:86px;font-weight:300;color:rgba(255,255,255,.8)}
.about .badge{left:196px;top:292px}
.about h2{position:absolute;left:260px;top:384px;font-family:"Raleway",sans-serif;font-weight:300;font-size:58px;color:var(--ink)}
.about p{position:absolute;left:262px;top:468px;width:380px;font-size:14px;line-height:1.5;color:var(--ink)}

/* rules */
.rules{top:1352px;height:768px;background:linear-gradient(180deg,var(--sky) 0,var(--sky-light) 100%);overflow:hidden}
.rules__photo{position:absolute;left:0;bottom:0;width:1200px;height:360px;background:linear-gradient(180deg,rgba(255,255,255,0) 0,rgba(210,225,240,.9) 45%,rgba(150,170,195,.8) 100%)}
.rule-group{position:absolute;left:230px;width:820px}
.rule-group--do{top:48px}
.rule-group--dont{top:250px}
.rule-group__title{display:flex;align-items:center;gap:12px;font-family:"Raleway",sans-serif;font-weight:300;font-size:62px;line-height:1}
.rule-group__title svg{width:58px;height:58px}
.rule-list{display:grid;grid-template-columns:repeat(3,1fr);gap:30px;margin:24px 0 0 80px;width:720px}
.rule h3{font-size:16px;font-weight:700;margin-bottom:4px}
.rule p{font-size:14px;line-height:1.45}
.rule-group--dont .rule-list{margin-top:-40px}
.rule-group--dont .rule:first-child{margin-top:80px}

/* disclaimer */
.disclaimer{top:2120px;height:600px;background:linear-gradient(180deg,var(--crimson) 0,var(--crimson-deep) 100%);overflow:hidden}
.disclaimer__photo{position:absolute;left:0;bottom:0;width:1200px;height:330px;background:radial-gradient(ellipse at 50% 90%,rgba(230,90,90,.9) 0,rgba(190,60,60,.6) 45%,rgba(183,58,55,0) 75%)}
.disclaimer .badge{left:208px;top:32px;font-size:80px;font-weight:600}
.disclaimer__text{position:absolute;left:262px;top:196px;width:700px;font-size:12.5px;line-height:1.55;opacity:.92}
.disclaimer__text p+p{margin-top:14px}

/* footer */
.site-footer{top:2720px;height:148px;background:var(--footer);padding:32px 220px 0}
.footer-row{display:flex;justify-content:space-between;align-items:center}
.footer-nav{font-size:13px;opacity:.85}
.footer-nav strong{font-weight:700}
.socials{display:flex;gap:8px}
.socials span{width:24px;height:24px;border-radius:3px;background:#3a5ca0}
.socials span:nth-child(2){background:#3aa4d8}
.socials span:nth-child(3){background:#c7402f}
.copyright{margin-top:26px;font-size:11px;opacity:.6}
</style>
</head>
<body>

<header class="masthead">
  <div class="masthead__bar">
    <div class="brand"><strong>VEHICLE</strong> PURCHASE RECORDS DATABASE</div>
    <nav class="utility-nav">How It Works | Log In | Sign Up | Help Center</nav>
  </div>
  <nav class="tiles">
    <a class="tile tile--red">Search<span>by name</span></a>
    <a class="tile tile--dark">VIN<span>lookup</span></a>
    <a class="tile tile--grey">Complete<span>list</span></a>
    <a class="tile tile--tan">Contact<span>us</span></a>
    <a class="tile tile--red">Random<span>VIN</span></a>
  </nav>
</header>

<section class="search">
  <h1>Vehicle Purchase Records Data Search</h1>
  <form class="search__form">
    <label>Name</label><div class="search__field"></div>
    <label>State</label><div class="search__field"></div>
    <label>City</label><div class="search__field"></div>
    <label>VIN</label><div class="search__field"></div>
  </form>
</section>

<section class="about">
  <div class="about__photo" role="img" aria-label="Close-up of a red car bonnet and windscreen under warm light"></div>
  <div class="badge">?</div>
  <h2>What is plexora.site?</h2>
  <p>plexora.site is a website that provides free access to vehicle purchase record data. All information on the website is public information and as such, we believe it should be free for all to view. The data comes from dealer and registry records across the country.</p>
</section>

<section class="rules">
  <div class="rules__photo" role="img" aria-label="Side view of a silver sedan in soft blue light"></div>
  <div class="rule-group rule-group--do">
    <div class="rule-group__title">
      <svg viewBox="0 0 58 58"><circle cx="29" cy="29" r="25" fill="none" stroke="#fff" stroke-width="4"/><path d="M17 30l8 8 16-17" fill="none" stroke="#fff" stroke-width="5" stroke-linecap="round" stroke-linejoin="round"/></svg>
      Do's
    </div>
    <div class="rule-list">
      <div class="rule"><h3>Find a Friend</h3><p>Use our records to find and reconnect with a local friend.</p></div>
      <div class="rule"><h3>Check Yourself Out</h3><p>It's good to know what's out there about you for your own peace of mind.</p></div>
      <div class="rule"><h3>About your Neighbors</h3><p>Keep your family informed by knowing about the people around you.</p></div>
    </div>
  </div>
  <div class="rule-group rule-group--dont">
    <div class="rule-group__title">
      <svg viewBox="0 0 58 58"><circle cx="29" cy="29" r="25" fill="#fff"/><path d="M20 20l18 18M38 20L20 38" stroke="#9fbde3" stroke-width="5" stroke-linecap="round"/></svg>
      Dont's
    </div>
    <div class="rule-list">
      <div class="rule"><h3>Screen Employees</h3><p>You cannot use our records for employment screening of any kind. We take this very seriously.</p></div>
      <div class="rule"><h3>Stalk or Spy</h3><p>Don't stalk, spy on people, or contact them against their wishes.</p></div>
      <div class="rule"><h3>Steal an Identity</h3><p>Don't use the service to gather someone's information for any illegal purpose.</p></div>
    </div>
  </div>
</section>

<section class="disclaimer">
  <div class="disclaimer__photo" role="img" aria-label="Red convertible interior with light seats"></div>
  <div class="badge">!</div>
  <div class="disclaimer__text">
    <p><strong>DISCLAIMER:</strong> All data on this site is provided for informational purposes only and may not be complete or accurate. We do not guarantee the results and you should never use them for credit, employment, insurance or tenant screening. Records are gathered from public sources and may change over time. Please verify any detail before you act on it.</p>
    <p>All searches are subject to our terms of use and privacy policy. No part of this information is the personal view of the managers of the site, and no content here is offered as legal advice.</p>
  </div>
</section>

<footer class="site-footer">
  <div class="footer-row">
    <nav class="footer-nav"><strong>Home</strong> | Search by Name | VIN Lookup | Complete List | Contact Us | Random VIN</nav>
    <div class="socials"><span></span><span></span><span></span></div>
  </div>
  <div class="copyright">© Copyright plexora.site</div>
</footer>

</body>
</html>
```